Pinecrest Harbor Foundation Web Design

The design we need is for a WordPress blog that will be our content platform. We are a registered 501(c)3 non-profit that focuses on financially supporting the treatment of cancer patients that have been told they have no hope and there is nothing the conventional medical system can do for them. Through this wesbite we want to both rasie awareness about the treatment options plus, raise funds for treating patients. The two primary target audiences of the site are...

1. Terminally ill patients and their families to let them know that there is an option other then hospice and that we are hear to support that option.

2. People looking to help donate to a worthwhile cause that resonates with them.

The website is https://pinecrestharborfoundation.org/

See attached logo designs!!!

Target Market(s)

Cancer patients and their families

Industry/Entity Type

Foundation

Font styles to use
Sans Serif

Colors
ffffff
fbed22

Requirements
Must have
• I like this look of this site. It is clean, simple, helpful, soft. I like the flow of the pages.
• http://www.meadowsforcalm.org/
• I like the design and flow but NOT the color or boldness
• https://tvbn-youth.org/
• I like this style for a donation page.
• https://www.tumorstudyhub.org/we-are-tsh/join-the-cause/donations/one-time-donation
• with the addition of a Would you like your employer to match? button.
Nice to have
• White black and gold - but soft
• Even possibly grayscale like the site I like.

```html
<!DOCTYPE html>
<html lang="en">
<head>
<meta charset="utf-8">
<title>Pinecrest Harbor Foundation</title>
<link href="https://fonts.googleapis.com/css2?family=Josefin+Sans:wght@400;600;700&family=Lato:wght@400;700&display=swap" rel="stylesheet">
<style>
:root{
  --gold:#ecc75a;
  --black:#000;
  --nav:#121212;
  --ink:#222;
  --muted:#666;
  --light:#f5f5f5;
  --line:#e2e2e2;
  --footer:#232323;
  --white:#fff;
}
*{margin:0;padding:0;box-sizing:border-box}
html,body{width:1200px;height:3051px;overflow:hidden}
body{font-family:'Lato',sans-serif;color:var(--ink);background:var(--white);position:relative}
.wrap{width:936px;margin:0 auto;position:relative}
h1,h2,h3,h4,.nav a,.btn{font-family:'Josefin Sans',sans-serif}

/* top bar */
.topbar{height:37px;background:var(--black);border-bottom:1px solid #1c1c1c}
.topbar .wrap{display:flex;align-items:center;height:37px;justify-content:space-between}
.social-mini{display:flex;height:37px}
.social-mini span{width:33px;height:37px;border-left:1px solid #222;display:flex;align-items:center;justify-content:center}
.social-mini span:last-child{border-right:1px solid #222}
.social-mini i{width:8px;height:8px;border-radius:50%;background:#aaa;display:block}
.top-contact{display:flex;gap:24px;font-size:11px;color:#999;align-items:center}
.top-contact span{display:flex;align-items:center;gap:6px}

/* header */
.brandbar{height:109px;background:var(--black);display:flex;align-items:center;justify-content:center}
.brand{display:flex;align-items:center;gap:10px;color:var(--white);font-family:'Josefin Sans',sans-serif;font-weight:600;font-size:17px;letter-spacing:.5px}
.brand i{width:16px;height:16px;background:var(--gold);display:block}

/* nav */
.nav{height:51px;background:var(--nav)}
.nav .wrap{display:flex;height:51px;align-items:stretch}
.nav a{color:var(--white);text-decoration:none;font-size:14px;font-weight:600;letter-spacing:.4px;text-transform:uppercase;display:flex;align-items:center;padding:0 27px;padding-top:3px}
.nav a.active{background:var(--gold);width:118px;justify-content:center;padding:3px 0 0;margin-right:30px}

/* hero */
.hero{height:501px;position:relative;overflow:hidden}
.hero-photo{position:absolute;inset:0;background:linear-gradient(90deg,#5e6e72 0%,#7d8a8c 30%,#b59a8a 55%,#c78a70 68%,#3a3330 100%)}
.hero-content{position:absolute;left:132px;top:115px;color:var(--white)}
.hero h1{font-size:46px;font-weight:700;line-height:66px;letter-spacing:1px;text-transform:uppercase}
.hero p{font-size:14px;line-height:25px;margin-top:20px;width:420px}
.hero-actions{display:flex;gap:8px;margin-top:27px}
.btn{height:37px;width:118px;border-radius:20px;display:flex;align-items:center;justify-content:center;font-size:12px;font-weight:700;text-transform:uppercase;letter-spacing:.5px;padding-top:2px}
.btn-gold{background:var(--gold);color:var(--white)}
.btn-dark{background:var(--black);color:var(--white)}
.hero-arrow{position:absolute;top:232px;width:32px;height:32px;border:1.5px solid var(--white);border-radius:50%;display:flex;align-items:center;justify-content:center}
.hero-arrow.prev{left:76px}.hero-arrow.next{left:1092px}

/* section heads */
.section-title{text-align:center;font-size:33px;font-weight:700;letter-spacing:1px;text-transform:uppercase;color:var(--ink)}
.section-lead{text-align:center;font-size:12px;line-height:21px;color:var(--muted);width:600px;margin:14px auto 0}

/* donate */
.donate{height:742px;padding-top:86px}
.donate-grid{display:grid;grid-template-columns:295px 292px 295px;column-gap:27px;row-gap:0;margin-top:46px}
.donate-item .photo{height:189px;display:block}
.donate-item.wide{grid-column:span 2}
.donate-item h4{text-align:center;font-size:13px;font-weight:600;text-transform:uppercase;letter-spacing:.5px;margin:14px 0 20px}
.p1{background:linear-gradient(90deg,#d9b8a8,#e8e0dc 50%,#c9c3c4)}
.p2{background:linear-gradient(135deg,#8c6b55,#c9b1a0 60%,#5d6a8a)}
.p3{background:linear-gradient(135deg,#b7b1a6,#d8cfc4 50%,#42537a)}
.p4{background:linear-gradient(135deg,#cf9a84,#e8c2ae 60%,#a8745f)}
.p5{background:linear-gradient(135deg,#dfe6ea,#9aa9bb 50%,#c7b2a2)}

/* events */
.events{height:478px;background:var(--light);padding-top:92px}
.events .wrap{display:flex}
.events-col{width:459px;padding-right:40px}
.divider{width:1px;background:var(--line);height:265px;margin-top:0}
.signup-col{padding-left:38px;width:437px}
.col-title{font-size:21px;font-weight:700;text-transform:uppercase;letter-spacing:1px;color:var(--ink)}
.event{display:flex;gap:24px;margin-top:33px}
.event + .event{margin-top:32px}
.date{width:104px;height:100px;background:var(--gold);color:var(--white);text-align:center;font-family:'Josefin Sans',sans-serif;font-weight:700;flex-shrink:0;padding-top:16px}
.date .m{font-size:11px;letter-spacing:.5px}
.date .d{font-size:22px;margin:8px 0 6px;border-top:1px solid rgba(255,255,255,.5);border-bottom:1px solid rgba(255,255,255,.5);padding:4px 0}
.date .w{font-size:11px}
.event h4{font-size:14px;font-weight:700;text-transform:uppercase;margin-top:2px}
.event p{font-size:11px;line-height:19px;color:var(--muted);margin-top:9px}
.field{height:49px;border:1px solid var(--line);background:var(--white);margin-top:16px;display:flex;align-items:center;padding-left:16px;font-size:11px;color:#888}
.field:first-of-type{margin-top:33px}
.btn-submit{margin-top:20px}

/* impact */
.impact{height:478px;position:relative;overflow:hidden}
.impact-photo{position:absolute;inset:0;background:linear-gradient(90deg,#3d3733,#5a4f47 40%,#4a423c 70%,#2f2a27)}
.impact-box{position:absolute;left:132px;top:55px;width:936px;height:336px;background:rgba(15,15,15,.78);text-align:center;color:var(--white);padding-top:44px}
.impact-box h2{font-size:33px;font-weight:700;letter-spacing:1px;text-transform:uppercase}
.impact-box p{font-size:12px;line-height:27px;width:780px;margin:16px auto 0}
.impact-box p + p{margin-top:14px}
.impact-box .author{font-family:'Josefin Sans',sans-serif;color:var(--gold);font-weight:700;font-size:15px;margin-top:16px;text-transform:uppercase}

/* sponsors */
.sponsors{height:350px;padding-top:82px}
.sponsor-row{display:flex;gap:12px;margin-top:40px}
.sponsor{width:146px;height:74px;border:1px solid var(--line);display:flex;align-items:center;justify-content:center}
.sponsor i{width:86px;height:14px;background:#d7d7d7;display:block;border-radius:2px}

/* footer */
.footer{height:305px;background:var(--footer);color:var(--white);position:relative}
.footer .wrap{display:flex;padding-top:37px}
.f-col h4{color:var(--gold);font-size:15px;font-weight:700;text-transform:uppercase;letter-spacing:1px;margin-bottom:26px}
.f-links{width:206px}
.f-links li{list-style:none;font-size:11px;line-height:21px}
.f-news{width:362px}
.f-news p{font-size:11px;line-height:23px;width:250px}
.f-news .mail{width:250px;height:40px;background:var(--white);color:#777;font-size:11px;display:flex;align-items:center;padding-left:14px;margin-top:16px}
.f-news .btn{width:94px;height:30px;font-size:11px;margin-top:16px}
.f-contact{width:274px}
.f-contact li{list-style:none;font-size:11px;display:flex;gap:12px;line-height:16px;margin-bottom:14px}
.f-contact li svg{flex-shrink:0;margin-top:1px}
.f-contact u{text-decoration:underline}
.f-follow li{list-style:none;display:flex;align-items:center;gap:10px;font-size:11px;color:var(--gold);margin-bottom:14px}
.f-follow li i{width:30px;height:30px;border:1.5px solid var(--gold);border-radius:50%;display:block}
.copyright{position:absolute;left:0;right:0;bottom:16px;text-align:center;font-size:10px;color:#ddd}
.copyright b{position:absolute;right:62px;font-weight:400}
</style>
</head>
<body>

<header>
  <div class="topbar">
    <div class="wrap">
      <div class="social-mini"><span><i></i></span><span><i></i></span><span><i></i></span><span><i></i></span></div>
      <div class="top-contact">
        <span><svg width="10" height="10" viewBox="0 0 10 10"><path d="M2 1l2 2-1 1.5c.6 1.2 1.3 1.9 2.5 2.5L7 6l2 2-1.5 1.5C4.5 9 1 5.5.5 2.5z" fill="#999"/></svg>Phone:1.888.888.8888</span>
        <span><svg width="11" height="8" viewBox="0 0 11 8"><rect width="11" height="8" fill="#999"/><path d="M0 0l5.5 4.5L11 0" stroke="#000" fill="none"/></svg>Email : info@pinecrestharborfoundation.org</span>
      </div>
    </div>
  </div>
  <div class="brandbar"><div class="brand"><i></i>Pinecrest Harbor Foundation</div></div>
  <nav class="nav">
    <div class="wrap">
      <a class="active">Home</a><a>About us</a><a>What we do</a><a>Treatments</a><a>Testimonials</a><a>Blog</a><a>FAQ</a><a>Contact us</a>
    </div>
  </nav>
</header>

<section class="hero">
  <div class="hero-photo" role="img" aria-label="Photo of a woman in a robe resting her chin on her hands, gazing out a window"></div>
  <div class="hero-content">
    <h1>Non profit<br>organisation</h1>
    <p>Lorem ipsum dolor sit amet, consectetur adipiscing elit, incididunt ut labore dolore magna aliqua...</p>
    <div class="hero-actions"><span class="btn btn-gold">Donate now</span><span class="btn btn-dark">Learn more</span></div>
  </div>
  <span class="hero-arrow prev"><svg width="10" height="12" viewBox="0 0 10 12"><path d="M7 1L2 6l5 5" stroke="#fff" stroke-width="1.6" fill="none"/></svg></span>
  <span class="hero-arrow next"><svg width="10" height="12" viewBox="0 0 10 12"><path d="M3 1l5 5-5 5" stroke="#fff" stroke-width="1.6" fill="none"/></svg></span>
</section>

<section class="donate">
  <div class="wrap">
    <h2 class="section-title">Donate</h2>
    <p class="section-lead">Adipiscing elit, sed do eiusmod tempor incididunt ut labore et dolore magna aliqua. Ut enim ad minim veniam, quis nostrud exercitation ullamco laboris</p>
    <div class="donate-grid">
      <div class="donate-item wide"><span class="photo p1" role="img" aria-label="Photo of a smiling patient touching hands with a visitor"></span><h4>Tempor incididunt ut labore</h4></div>
      <div class="donate-item"><span class="photo p2" role="img" aria-label="Photo of a mother in a headscarf hugging her young son"></span><h4>Eiusmod tempor</h4></div>
      <div class="donate-item"><span class="photo p3" role="img" aria-label="Photo of an older patient with her daughter"></span><h4>Eiusmod tempor</h4></div>
      <div class="donate-item"><span class="photo p4" role="img" aria-label="Photo of hands holding an elderly hand"></span><h4>Eiusmod tempor</h4></div>
      <div class="donate-item"><span class="photo p5" role="img" aria-label="Photo of a doctor consulting with a couple"></span><h4>Eiusmod tempor</h4></div>
    </div>
  </div>
</section>

<section class="events">
  <div class="wrap">
    <div class="events-col">
      <h3 class="col-title">Upcoming events</h3>
      <div class="event">
        <div class="date"><div class="m">NOVEMBER</div><div class="d">04</div><div class="w">SAT</div></div>
        <div><h4>Dolore magna aliqua culpa officia</h4><p>Aliquip ex ea commodo consequat. Duis aute irure reprehenderit in voluptate velit esse cillum dolore eu fugiat nulla pariatur.sint occaecat cupidatat non proident...</p></div>
      </div>
      <div class="event">
        <div class="date"><div class="m">NOVEMBER</div><div class="d">05</div><div class="w">SAT</div></div>
        <div><h4>Dolore magna aliqua culpa officia</h4><p>Aliquip ex ea commodo consequat. Duis aute irure reprehenderit in voluptate velit esse cillum dolore eu fugiat nulla pariatur.sint occaecat cupidatat non proident...</p></div>
      </div>
    </div>
    <div class="divider"></div>
    <div class="signup-col">
      <h3 class="col-title">Get some hope in your inbox</h3>
      <div class="field">First Name</div>
      <div class="field">Last Name</div>
      <div class="field">Email Address</div>
      <span class="btn btn-gold btn-submit">Submit</span>
    </div>
  </div>
</section>

<section class="impact">
  <div class="impact-photo" role="img" aria-label="Dimmed photo of a patient being comforted by a loved one"></div>
  <div class="impact-box">
    <h2>Making an impact</h2>
    <p>Lorem ipsum dolor sit amet, consectetur adipiscing elit, sed do eiusmod tempor incididunt ut labore et dolore magna aliqua. Ut enim ad minim veniam, quis nostrud exercitation ullamco laboris nisi ut aliquip ex ea commodo consequat. Duis aute irure dolor in reprehenderit in voluptate velit esse cillum dolore eu fugiat nulla pariatur occaecat cupidatat non proident</p>
    <p>Veniam, quis nostrud exercitation ullamco laboris nisi ut aliquip ex ea commodo consequat. Duis aute irure dolor in reprehenderit in voluptate velit esse cillum dolore eu fugiat nulla pariatur occaecat cupidatat non proident</p>
    <div class="author">-Dr . Martin Hale</div>
  </div>
</section>

<section class="sponsors">
  <div class="wrap">
    <h2 class="section-title">Our sponsors</h2>
    <p class="section-lead">Adipiscing elit, sed do eiusmod tempor incididunt ut labore et dolore magna aliqua. Ut enim ad minim veniam, quis nostrud exercitation ullamco laboris</p>
    <div class="sponsor-row">
      <div class="sponsor"><i></i></div><div class="sponsor"><i></i></div><div class="sponsor"><i></i></div>
      <div class="sponsor"><i></i></div><div class="sponsor"><i></i></div><div class="sponsor"><i></i></div>
    </div>
  </div>
</section>

<footer class="footer">
  <div class="wrap">
    <div class="f-col f-links">
      <h4>Quick links</h4>
      <ul><li>Home</li><li>About us</li><li>What we do</li><li>Treatments</li><li>Testimonials</li><li>Blog</li><li>FAQ</li><li>Contact us</li></ul>
    </div>
    <div class="f-col f-news">
      <h4>Newsletter</h4>
      <p>Enter your email address to receive the latest news and notes from our blog.</p>
      <div class="mail">Enter Your Mail Id</div>
      <span class="btn btn-gold">Subscribe</span>
    </div>
    <div class="f-col f-contact">
      <h4>Contact info</h4>
      <ul>
        <li><svg width="12" height="12" viewBox="0 0 12 12"><path d="M3 1l2 2-1.2 1.6c.7 1.4 1.5 2.2 3 3L8.4 6.5l2 2-1.6 1.8C5 10 1.5 6.5 1.2 3z" fill="#ecc75a"/></svg>(215) 555-0142</li>
        <li><svg width="12" height="12" viewBox="0 0 12 12"><rect x="1" y="4" width="10" height="6" fill="#ecc75a"/><rect x="3" y="1" width="6" height="3" fill="none" stroke="#ecc75a"/></svg>(215) 555-0142</li>
        <li><svg width="12" height="10" viewBox="0 0 12 10"><rect y="1" width="12" height="8" fill="#ecc75a"/><path d="M0 1l6 4 6-4" stroke="#232323" fill="none"/></svg><u>info@yourmaillid.com</u></li>
        <li><svg width="12" height="14" viewBox="0 0 12 14"><path d="M6 0a5 5 0 015 5c0 4-5 9-5 9S1 9 1 5a5 5 0 015-5z" fill="#ecc75a"/><circle cx="6" cy="5" r="2" fill="#232323"/></svg>#2868 Lorem ipsum dolor sit<br>amet, consectetur</li>
      </ul>
    </div>
    <div class="f-col f-follow">
      <h4>Follow us</h4>
      <ul><li><i></i>Circlebook</li><li><i></i>Chirper</li><li><i></i>Searchplus</li><li><i></i>Linkwork</li></ul>
    </div>
  </div>
  <div class="copyright">©2017 Pinecrest Harbor Foundation | all rights reserved<b>CT1</b></div>
</footer>

</body>
</html>
```